New Business Card Design Project

Use the flyer uploaded and website www.brightoakbuilders.com for inspiration.
List Our Services on Backside of business cards
Marcus Delling
Harborline Builders Inc.
Licensed General Contractors
858-471-6093

Contact Information for Business Card

Use the flyer uploaded and website www.brightoakbuilders.com for inspiration. List Our Services on Backside of business cards Marcus Delling Harborline Builders Inc. Licensed General Contractors 858-471-6093

```html
<!DOCTYPE html>
<html lang="en">
<head>
<meta charset="UTF-8">
<title>Harborline Builders – Business Card</title>
<link href="https://fonts.googleapis.com/css2?family=Montserrat:wght@400;500;700&display=swap" rel="stylesheet">
<style>
  :root {
    --backdrop: #2b2b2e;
    --card: #141414;
    --ink: #f2f2f2;
    --ink-soft: #d9d9d9;
    --rule: #cfcfcf;
  }
  * { box-sizing: border-box; margin: 0; padding: 0; }
  html, body { width: 1200px; height: 900px; overflow: hidden; }
  body {
    background: var(--backdrop);
    font-family: 'Montserrat', sans-serif;
    color: var(--ink);
    display: flex;
    flex-direction: column;
    align-items: center;
    justify-content: center;
    gap: 40px;
  }
  .card {
    width: 700px;
    height: 400px;
    background: var(--card);
    border-radius: 22px;
    position: relative;
    box-shadow: 0 14px 30px rgba(0,0,0,0.45);
  }
  .brand {
    position: absolute;
    left: 60px;
    top: 170px;
    width: 260px;
    display: flex;
    align-items: center;
    gap: 12px;
  }
  .brand-mark {
    width: 14px; height: 14px;
    border: 1.5px solid var(--ink);
    flex: none;
  }
  .brand-name {
    font-weight: 400;
    font-size: 21px;
    letter-spacing: 0.06em;
    text-transform: uppercase;
    color: var(--ink);
  }
  /* back side */
  .divider {
    position: absolute;
    left: 355px;
    top: 95px;
    width: 1.5px;
    height: 210px;
    background: var(--rule);
  }
  .services {
    position: absolute;
    left: 385px;
    top: 78px;
  }
  .services-title {
    font-weight: 700;
    font-size: 20px;
    margin-bottom: 8px;
  }
  .services-list {
    list-style: none;
    font-size: 14.5px;
    line-height: 23px;
    color: var(--ink-soft);
  }
  .services-list li::before {
    content: "";
    display: inline-block;
    width: 5px; height: 5px;
    border-radius: 50%;
    background: var(--ink);
    margin-right: 9px;
    vertical-align: middle;
  }
  /* front side */
  .contact {
    position: absolute;
    left: 390px;
    top: 80px;
  }
  .person-name {
    font-weight: 700;
    font-size: 27px;
    line-height: 1.1;
  }
  .person-role {
    font-size: 14.5px;
    color: var(--ink-soft);
    margin-top: 2px;
  }
  .address {
    font-size: 14.5px;
    line-height: 20px;
    color: var(--ink-soft);
    margin-top: 26px;
  }
  .contact-lines {
    list-style: none;
    margin-top: 22px;
    font-size: 14.5px;
    color: var(--ink-soft);
  }
  .contact-lines li {
    display: flex;
    align-items: center;
    gap: 12px;
    height: 26px;
  }
  .contact-lines svg { width: 16px; height: 16px; flex: none; }
</style>
</head>
<body>

  <section class="card card-back">
    <div class="brand">
      <span class="brand-mark"></span>
      <span class="brand-name">Harborline Builders</span>
    </div>
    <div class="divider"></div>
    <div class="services">
      <h2 class="services-title">Our Services</h2>
      <ul class="services-list">
        <li>Remodel: Kitchen &amp; Bath</li>
        <li>Painting: Interior &amp; Exterior</li>
        <li>Flooring: Carpet, Vinyl, Wood</li>
        <li>Window &amp; Door Replacement</li>
        <li>Plumbing: Repair &amp; Upgrades</li>
        <li>Energy Efficienct Upgrades</li>
        <li>Deck &amp; Patio construction</li>
        <li>Water &amp; Mold Damage</li>
        <li>Garage Renovation</li>
      </ul>
    </div>
  </section>

  <section class="card card-front">
    <div class="brand">
      <span class="brand-mark"></span>
      <span class="brand-name">Harborline Builders</span>
    </div>
    <div class="contact">
      <h1 class="person-name">Marcus Delling</h1>
      <p class="person-role">Licensed General Contractors</p>
      <p class="address">74 Larkspur Avenue, suite 208<br>Alden PA 18522</p>
      <ul class="contact-lines">
        <li>
          <svg viewBox="0 0 16 16" aria-hidden="true"><path d="M2 5c0-2 2-3 6-3s6 1 6 3v1h-3V4.8H5V6H2z M4 7h8l2 7H2z" fill="#f2f2f2"/><circle cx="8" cy="10.5" r="1.8" fill="#141414"/></svg>
          858-471-6093
        </li>
        <li>
          <svg viewBox="0 0 16 16" aria-hidden="true"><rect x="1" y="3" width="14" height="10" rx="1" fill="#f2f2f2"/><path d="M1.5 3.5 8 9l6.5-5.5" stroke="#141414" stroke-width="1.3" fill="none"/></svg>
          info@brightoakbuilders.com
        </li>
        <li>
          <svg viewBox="0 0 16 16" aria-hidden="true"><circle cx="8" cy="8" r="7" fill="#f2f2f2"/><ellipse cx="8" cy="8" rx="3" ry="7" fill="none" stroke="#141414" stroke-width="1.1"/><path d="M1 8h14" stroke="#141414" stroke-width="1.1"/></svg>
          www.brightoakbuilders.com
        </li>
      </ul>
    </div>
  </section>

</body>
</html>
```